Professional looking Roller Blind Discount Card that portrays quality at a value for money price!

We need a double sided business card designed as a discount card. Size 90mm wide x 55mm high.We would like it to look professional and portray quality at a value for money price point.I have uploaded a word document with a basic layout with the information we want included on each side of the card. Please put your own thought into the layout.

Contact Information for Business Card

As per word document attached.

```html
<!DOCTYPE html>
<html lang="en">
<head>
<meta charset="utf-8">
<title>Roller Blinds Discount Card</title>
<link rel="stylesheet" href="https://fonts.googleapis.com/css2?family=Lexend:wght@400;600;700&display=swap">
<style>
  :root {
    --ink: #0b0b0b;
    --paper: #f7f7f5;
    --backdrop: #d9d6d0;
    --photo-warm: #6e5d52;
    --photo-green: #5f7a4a;
  }
  * { box-sizing: border-box; margin: 0; padding: 0; }
  html, body { width: 1200px; height: 843px; overflow: hidden; }
  body {
    background: var(--backdrop);
    font-family: "Lexend", "Helvetica Neue", Arial, sans-serif;
    position: relative;
  }
  .card {
    position: absolute;
    top: 256px;
    width: 540px;
    height: 330px;
    border-radius: 4px;
    overflow: hidden;
    box-shadow: 0 6px 18px rgba(0,0,0,0.18);
  }
  .card--front { left: 40px; background: var(--paper); color: var(--ink); }
  .card--back { left: 620px; background: var(--ink); color: var(--paper); }
  .abs { position: absolute; }

  /* Front */
  .front-title { top: 22px; left: 0; width: 100%; text-align: center; font-size: 46px; font-weight: 700; letter-spacing: 0.5px; }
  .front-sub { top: 84px; left: 0; width: 100%; text-align: center; font-size: 23px; font-weight: 700; }
  .front-photo {
    top: 140px; left: 46px; width: 250px; height: 122px;
    border: 3px solid var(--ink);
    background: linear-gradient(90deg, var(--photo-warm) 0 34%, var(--photo-green) 34% 100%);
  }
  .fabric-box {
    top: 128px; left: 308px; width: 184px; height: 118px;
    background: var(--ink); color: var(--paper);
    font-size: 23px; font-weight: 700; line-height: 1.2;
    padding: 12px 0 0 16px;
  }
  .front-call { top: 272px; right: 46px; font-size: 19px; font-weight: 700; }
  .brand { bottom: 16px; left: 48px; display: flex; align-items: center; gap: 6px; font-size: 10px; font-weight: 600; letter-spacing: 0.5px; }
  .brand-mark { width: 14px; height: 14px; background: var(--ink); }

  /* Back */
  .offer { top: 20px; left: 0; width: 100%; text-align: center; font-size: 46px; font-weight: 700; }
  .offer-line { top: 82px; left: 0; width: 100%; text-align: center; font-size: 22px; font-weight: 700; }
  .offer-types { top: 114px; left: 60px; font-size: 22px; font-weight: 700; word-spacing: 10px; }
  .pill {
    position: absolute; height: 26px; border-radius: 13px;
    background: var(--paper); color: var(--ink);
    font-size: 14px; font-weight: 700; line-height: 26px; white-space: nowrap;
  }
  .badge {
    position: absolute; width: 70px; height: 70px; border-radius: 50%;
    background: var(--paper); color: var(--ink);
    display: flex; align-items: center; justify-content: center;
    font-size: 15px; font-weight: 700;
  }
  .pill--measure { top: 166px; left: 90px; width: 250px; padding-left: 22px; }
  .badge--free { top: 160px; left: 40px; }
  .pill--price { top: 198px; left: 250px; width: 210px; padding-left: 16px; }
  .badge--price { top: 158px; left: 428px; }
  .pill--family { top: 230px; left: 140px; width: 210px; padding-left: 44px; }
  .badge--family { top: 222px; left: 104px; font-size: 13px; }
  .back-call { top: 272px; right: 40px; font-size: 19px; font-weight: 700; }
</style>
</head>
<body>
  <section class="card card--front" aria-label="Card front">
    <h1 class="abs front-title">Roller Blinds</h1>
    <p class="abs front-sub">FREE in Home Measure &amp; Quote</p>
    <div class="abs front-photo" role="img" aria-label="Photo of a room with roller blinds over garden windows"></div>
    <div class="abs fabric-box">Huge<br>Selection<br>of Fabrics</div>
    <p class="abs front-call">Call 0400 123 456 TODAY!</p>
    <div class="abs brand"><span class="brand-mark"></span><span>NORTHVALE PROJECTS</span></div>
  </section>

  <section class="card card--back" aria-label="Card back">
    <h2 class="abs offer">25% OFF</h2>
    <p class="abs offer-line">Quality Custom Made Roller Blinds</p>
    <p class="abs offer-types">Blackout Screen Light Filtering</p>

    <div class="pill pill--measure">in Home Measure &amp; Quote</div>
    <div class="badge badge--free">FREE</div>

    <div class="pill pill--price">Guaranteed Best</div>
    <div class="badge badge--price">PRICE</div>

    <div class="pill pill--family">Owned &amp; Operated</div>
    <div class="badge badge--family">FAMILY</div>

    <p class="abs back-call">Call 0400 123 456 TODAY!</p>
  </section>
</body>
</html>
```